Tovimar Community Development Planning New web site

Design a new web site. I have a budget of $1,500.00.
Attached on PowerPoint is a complete site plan. Home page and linked pages.
10 - 12 pages. All copy and photos will be supplied. (300dpi)
I have shown them the concept which they like.
No data bases required. Home page with animations dissolving.
They former web site has been taken down. They have been in business 30 years in New Jersey
Colors teal blues and greens
There will be a new logo)being designed)
The text in home page copy will give you a detailed story what they are all about.

files have been approved for Tovimar, Inc.   Brenton is the designer

```html
<!DOCTYPE html>
<html lang="en">
<head>
<meta charset="utf-8">
<title>Tovimar, Inc. – Our Company</title>
<link rel="stylesheet" href="https://fonts.googleapis.com/css2?family=Ubuntu:ital,wght@0,300;0,400;0,500;0,700;1,400&display=swap">
<style>
  :root {
    --bg-deep: #0f233d;
    --bg-mid: #1d4775;
    --bg-light: #2a5e97;
    --green: #6dd55a;
    --green-dark: #4ea83f;
    --text: #e8eef6;
    --text-soft: #c9d5e4;
    --silver: #d7dde4;
    --search-bg: #1b3a60;
    --badge: rgba(210, 222, 236, 0.55);
  }
  * { margin: 0; padding: 0; box-sizing: border-box; }
  html, body { width: 1200px; height: 994px; overflow: hidden; }
  body {
    position: relative;
    font-family: "Ubuntu", sans-serif;
    color: var(--text);
    background: radial-gradient(ellipse 70% 60% at 55% 58%, var(--bg-light) 0%, var(--bg-mid) 45%, var(--bg-deep) 100%);
  }
  .abs { position: absolute; }

  .brand { left: 146px; top: 24px; font-size: 30px; font-weight: 700; letter-spacing: 2px; color: var(--silver); }
  .search { left: 856px; top: 28px; width: 198px; height: 25px; background: var(--search-bg); border-radius: 2px; }
  .search span { position: absolute; left: 16px; top: 6px; font-size: 11px; font-style: italic; color: #9fb2c8; }
  .search svg { position: absolute; right: 8px; top: 5px; }

  .nav { left: 146px; top: 80px; width: 908px; height: 41px; background: var(--green); border-radius: 2px; display: flex; padding-left: 49px; }
  .nav a { display: block; height: 41px; line-height: 41px; padding: 0 15px; font-size: 11px; font-weight: 500; color: #fff; text-decoration: none; margin-right: 14px; }
  .nav a.active { background: var(--green-dark); margin-left: -15px; }

  .section-title { font-size: 22px; font-weight: 300; color: #fff; }
  .about-title { left: 145px; top: 168px; }
  .about-copy { left: 146px; top: 224px; width: 420px; font-size: 11.6px; line-height: 14.4px; color: var(--text); }
  .about-copy p { margin-bottom: 14.4px; }
  .about-photo { left: 614px; top: 218px; width: 441px; height: 262px; border: 2px solid #fff; border-radius: 3px; background: linear-gradient(135deg, #dfe6ee 0%, #8fa9c6 35%, #3e5f8e 65%, #1f2f44 100%); }

  .refs-title { left: 145px; top: 540px; }
  .ref { top: 590px; width: 283px; height: 170px; }
  .ref .open, .ref .close { position: absolute; font-family: Georgia, serif; font-weight: 700; font-size: 58px; line-height: 1; color: #fff; }
  .ref .open { left: -2px; top: -4px; }
  .ref .close { right: 0; top: 76px; }
  .ref p { position: absolute; left: 0; top: 18px; width: 283px; font-size: 11px; line-height: 13.6px; text-indent: 40px; }
  .ref .name { position: absolute; right: 2px; top: 137px; font-size: 11px; font-weight: 500; text-align: right; line-height: 14px; }
  .ref .role { display: block; font-weight: 400; font-style: italic; }

  .read-more { left: 992px; top: 802px; font-size: 11px; color: #fff; }

  .members { left: 146px; top: 894px; font-size: 13px; color: var(--text-soft); }
  .members b { font-weight: 700; }
  .badge { background: var(--badge); }

  .footer { left: 0; top: 952px; width: 1200px; height: 42px; background: var(--green); color: #fff; font-size: 13px; }
  .footer .item { position: absolute; top: 13px; display: flex; align-items: center; gap: 8px; }
</style>
</head>
<body>
  <div class="abs brand">TOVIMAR</div>
  <div class="abs search">
    <span>Search</span>
    <svg width="14" height="14" viewBox="0 0 14 14"><circle cx="8" cy="6" r="4" fill="none" stroke="#c9d5e4" stroke-width="1.5"/><line x1="5" y1="9" x2="1.5" y2="12.5" stroke="#c9d5e4" stroke-width="1.8"/></svg>
  </div>

  <nav class="abs nav">
    <a href="#">HOME</a>
    <a href="#" class="active" style="margin-left:0">OUR COMPANY</a>
    <a href="#">SERVICES</a>
    <a href="#">HOUSING REHAB APPLICATION</a>
    <a href="#">AFFORDABLE APPLICATION</a>
    <a href="#">CONTACT US</a>
  </nav>

  <h1 class="abs section-title about-title">OUR COMPANY</h1>
  <div class="abs about-copy">
    <p>Tovimar, Inc stands for Community, Grants, Planning and Housing.&nbsp; We specialize in all aspects of affordable housing, planning, COAH compliance, and the procurement of grants and loans for our clients.</p>
    <p>Founded in 1975, Tovimar has grown to be the only full service affordable housing implementation company in New Jersey.&nbsp; Seasoned in all facets of community development, Tovimar boasts a team that includes professional planners, expert grant-writers, COAH certified housing specialists, licensed building inspectors, lead testers, and knowledgeable support staff. Client needs are promptly met with continuity, efficiency and individual attention to detail.</p>
    <p>Tovimar serves as the Administrative Agent for more than 1,700 affordable homes and has also supervised the rehabilitation of more than 2,500 homes.&nbsp; Tovimar grant writing team secures more than $15 million each year for our clients. More than $250 million has been realized to date for Tovimar clients.</p>
  </div>
  <div class="abs about-photo" role="img" aria-label="Photo of a project team in business attire reviewing building plans around a table"></div>

  <h2 class="abs section-title refs-title">REFERENCES</h2>

  <div class="abs ref" style="left:146px">
    <span class="open">&ldquo;</span>
    <p>Lorem ipsum dolor sit amet, consectetur adipis elit. Pellentesque lobortis accumsan ipsum eu feugiat. Nam vehicula lacus nec magna aliquet a consequat quat tincidunt. Curabitur dictum gravida odio, nec interdum libero molestie ac. Vivamus id nisl eu ante.</p>
    <span class="close">&rdquo;</span>
    <div class="name">JOHN MALCOLM DOE<span class="role">Major of Dream City</span></div>
  </div>
  <div class="abs ref" style="left:459px">
    <span class="open">&ldquo;</span>
    <p>Lorem ipsum dolor sit amet, consectetur adipis elit. Pellentesque lobortis accumsan ipsum eu feugiat. Nam vehicula lacus nec magna aliquet a consequat quat tincidunt. Curabitur dictum gravida odio, nec interdum libero molestie ac. Vivamus id nisl eu ante.</p>
    <span class="close">&rdquo;</span>
    <div class="name">JOHN MALCOLM DOE<span class="role">Major of Dream City</span></div>
  </div>
  <div class="abs ref" style="left:772px">
    <span class="open">&ldquo;</span>
    <p>Lorem ipsum dolor sit amet, consectetur adipis elit. Pellentesque lobortis accumsan ipsum eu feugiat. Nam vehicula lacus nec magna aliquet a consequat quat tincidunt. Curabitur dictum gravida odio, nec interdum libero molestie ac. Vivamus id nisl eu ante.</p>
    <span class="close">&rdquo;</span>
    <div class="name">JOHN MALCOLM DOE<span class="role">Major of Dream City</span></div>
  </div>

  <div class="abs read-more">READ MORE</div>

  <div class="abs members"><b>TOVIMAR</b> INC. IS A MEMBER OF:</div>
  <div class="abs badge" style="left:398px;top:889px;width:164px;height:26px;border-radius:2px"></div>
  <div class="abs badge" style="left:633px;top:879px;width:48px;height:48px"></div>
  <div class="abs badge" style="left:757px;top:872px;width:46px;height:62px;border-radius:3px"></div>
  <div class="abs badge" style="left:867px;top:886px;width:188px;height:30px;border-radius:2px"></div>

  <footer class="abs footer">
    <div class="item" style="left:146px">Copy Right 2014 &nbsp;&nbsp;<b>TOVIMAR</b> INC.</div>
    <div class="item" style="left:398px">
      <svg width="14" height="10" viewBox="0 0 14 10"><rect x="0.5" y="0.5" width="13" height="9" fill="none" stroke="#fff"/><polyline points="0.5,0.5 7,6 13.5,0.5" fill="none" stroke="#fff"/></svg>
      <span>218 Harbor Crest Lane, Seaview, New Jersey, 08790</span>
    </div>
    <div class="item" style="left:771px;top:10px">
      <svg width="12" height="20" viewBox="0 0 12 20"><rect x="1" y="1" width="10" height="18" rx="2" fill="none" stroke="#fff" stroke-width="1.5"/><line x1="4" y1="16" x2="8" y2="16" stroke="#fff"/></svg>
      <span style="margin-left:6px">(555) 014 2286</span>
    </div>
    <div class="item" style="left:920px;top:10px">
      <span style="font-size:18px;font-weight:700">@</span>
      <span>office@tovimarmail.com</span>
    </div>
  </footer>
</body>
</html>
```